Business Cards Design for the electrical wholesaler: clean bold dynamic :)

We need a business card design that would follow our latest brand guidelines. As an electrical wholesaler we want to bring a fresh look and feel into the industry. The design should be clean bold and dynamic. It should come alive with the renewed energy of our green colour. Our grey colour should keep things balanced and complement the notion of maturity and responsibility. We employ Lato as a corporate font however are not bound by this font and we’re open to interpretation here.

Target Market(s)

Electrical contractors

Industry/Entity Type

Business

Contact Information for Business Card

Logo
Name & Surname: Halyna Dorosh
Job Title: Director of Marketing
Email: halya.dorosh@quillmail.example
Cell phone: XXX.XXX.XXXX
Address: 20517 - 87 Ave. Edmonton, AB, Canada. T6K 4N8
Business Phone: 780.555.0184
Website: www.brovix.example

Font styles to use
Other font styles liked:
• Lato

Requirements
Must have
• Logo & website
Nice to have
• Brand elements - some of them you may find in the attached Brand Guidelines (e.g. three lines on the background signifying "W")

```html
<!DOCTYPE html>
<html lang="en">
<head>
<meta charset="utf-8">
<title>Brovix Business Card</title>
<link rel="stylesheet" href="https://fonts.googleapis.com/css2?family=Lato:ital,wght@0,300;0,400;0,700;1,300;1,400&display=swap">
<style>
  :root {
    --page-bg: #e9e7dc;
    --card-bg: #d9ecea;
    --brand-green: #7ee81e;
    --brand-grey: #465553;
    --ink: #1b1f1f;
    --ink-soft: #3a3f3f;
  }
  * { margin: 0; padding: 0; box-sizing: border-box; }
  html, body {
    width: 1200px; height: 1000px; overflow: hidden;
    background: var(--page-bg);
    font-family: "Lato", Arial, sans-serif;
  }
  .card {
    position: absolute; left: 398px; top: 133px;
    width: 418px; height: 733px;
    background: var(--card-bg);
    border-radius: 0 36px 0 36px;
    overflow: hidden;
  }
  .card-frame {
    position: absolute; left: 17px; top: 18px;
    width: 382px; height: 697px;
    border: 2.5px solid var(--brand-green);
    border-radius: 0 30px 0 30px;
    z-index: 2;
  }
  .corner-band { position: absolute; left: 0; bottom: 0; z-index: 1; }
  .brand {
    position: absolute; left: 0; right: 0; top: 122px;
    display: flex; align-items: center; justify-content: center; gap: 14px;
  }
  .brand-square { width: 40px; height: 40px; background: var(--brand-green); }
  .brand-name {
    font-size: 64px; font-weight: 400; color: var(--brand-grey);
    line-height: 1; letter-spacing: -1px;
  }
  .person { position: absolute; left: 0; right: 0; top: 268px; text-align: center; padding-left: 20px; }
  .person-name { font-size: 29px; font-weight: 400; color: var(--ink); line-height: 34px; }
  .person-title { font-size: 26px; font-weight: 300; font-style: italic; color: var(--ink); line-height: 28px; }
  .contact { position: absolute; left: 0; right: 0; top: 389px; text-align: center; padding-left: 20px;
    font-size: 20px; font-weight: 300; color: var(--ink-soft); line-height: 27px; }
  .contact-cell { letter-spacing: 0.5px; }
  .office { position: absolute; right: 29px; top: 594px; text-align: right; color: var(--ink); z-index: 3; }
  .office-address { font-size: 17px; font-weight: 400; line-height: 26px; letter-spacing: 0.3px; }
  .office-phone { font-size: 18px; font-weight: 400; margin-top: 10px; line-height: 24px; letter-spacing: 0.3px; }
  .office-web { font-size: 22px; font-weight: 700; color: var(--brand-green); line-height: 30px; margin-top: 4px; }
</style>
</head>
<body>
  <div class="card">
    <svg class="corner-band" width="120" height="90" viewBox="0 0 120 90" aria-hidden="true">
      <path d="M0 4 Q40 -6 60 10 L92 90 L0 90 Z" fill="var(--brand-grey)"/>
    </svg>
    <div class="card-frame"></div>

    <div class="brand">
      <span class="brand-square"></span>
      <span class="brand-name">brovix</span>
    </div>

    <div class="person">
      <p class="person-name">Halyna Dorosh</p>
      <p class="person-title">Director of Marketing</p>
    </div>

    <div class="contact">
      <p class="contact-email">halya.dorosh@quillmail.example</p>
      <p class="contact-cell">XXX.XXX.XXXX</p>
    </div>

    <div class="office">
      <p class="office-address">20517 - 87 Ave. Edmonton,<br>AB, Canada. T6K 4N8</p>
      <p class="office-phone">780.555.0184</p>
      <p class="office-web">www.brovix.example</p>
    </div>
  </div>
</body>
</html>
```